Need business card with a logo for a hearing aid sales and audiology business. We have two Hearing Instrument Specialists and one Audiologist on staff. Over 25 years in business. Locally owned and operated. Financing available. Most insurances accepted.

Summit Audio Wellness LLC
48730 W Larchmont, Suite 7
Spokane, WA 99281
509-617-2084
www.summitaudiowell.example

Manager
Tobias Kerrell HIS COHC
License #71829046

Target Market(s)

50yr old + people with a hearing loss.

Industry/Entity Type

Business

Contact Information for Business Card

48730 W Larchmont, Suite 7
Spokane, WA 99281
509-617-2084
www.summitaudiowell.example

Manager
Tobias Kerrell HIS COHC
NLVE #71829046

Font styles to use
Serif
Sans Serif

Requirements
Must have
• Business name, Tobias's name and title(s) and contact information, License #, web address

```html
<!DOCTYPE html>
<html lang="en">
<head>
<meta charset="utf-8">
<title>Summit Audio Wellness – Business Card</title>
<link href="https://fonts.googleapis.com/css2?family=Cinzel:wght@400&family=Josefin+Sans:wght@300;400&display=swap" rel="stylesheet">
<style>
  :root {
    --backdrop: #1c1c1c;
    --card: #f7f7f5;
    --green: #8cc63f;
    --green-soft: rgba(140, 198, 63, 0);
    --grey-text: #5f5f5f;
    --grey-light: #9b9b9b;
  }
  * { margin: 0; padding: 0; box-sizing: border-box; }
  html, body { width: 1200px; height: 800px; overflow: hidden; }
  body {
    background: var(--backdrop);
    font-family: "Josefin Sans", Arial, sans-serif;
    display: flex; align-items: center; justify-content: center;
  }
  .business-card {
    position: relative;
    width: 1000px; height: 572px;
    background: var(--card);
    border-radius: 34px;
    overflow: hidden;
  }
  .brand {
    position: absolute; left: 70px; top: 70px;
    display: flex; align-items: center; gap: 28px;
  }
  .brand-dot {
    width: 96px; height: 96px; border-radius: 50%;
    background: var(--green);
    flex: none;
  }
  .brand-name {
    font-family: "Cinzel", "Times New Roman", serif;
    font-weight: 400; font-size: 46px; line-height: 1.1; letter-spacing: 5px;
    text-transform: uppercase; color: var(--grey-light);
  }
  .person {
    position: absolute; left: 70px; top: 230px;
    color: var(--grey-text); font-weight: 300;
  }
  .person-name { font-size: 36px; color: var(--green); }
  .person-creds { font-size: 22px; color: var(--grey-text); margin-left: 6px; }
  .person-role, .person-license { font-size: 26px; line-height: 1.3; }
  .divider {
    position: absolute; left: 70px; top: 380px;
    width: 510px; height: 2px; background: var(--green);
  }
  .address {
    position: absolute; left: 70px; top: 400px;
    font-size: 26px; line-height: 1.3; font-weight: 300; color: var(--grey-text);
  }
  .contact-row {
    position: absolute; left: 70px; top: 496px;
    display: flex; align-items: center; gap: 40px;
    font-size: 28px; font-weight: 300; color: var(--grey-text);
  }
  .contact-item { display: flex; align-items: center; gap: 12px; }
  .web-domain { color: var(--green); }
  .icon { width: 28px; height: 28px; flex: none; }
  .corner-decoration {
    position: absolute; right: 0; bottom: 0;
    width: 300px; height: 380px;
    background: linear-gradient(135deg, var(--green-soft) 35%, var(--green) 100%);
  }
</style>
</head>
<body>
  <div class="business-card">
    <div class="brand">
      <span class="brand-dot"></span>
      <span class="brand-name">Summit Audio<br>Wellness</span>
    </div>

    <div class="person">
      <div><span class="person-name">Tobias Kerrell</span><span class="person-creds">HIS COHC</span></div>
      <div class="person-role">Manager</div>
      <div class="person-license">NLVE #71829046</div>
    </div>

    <div class="divider"></div>

    <div class="address">
      48730 W Larchmont, Suite 7<br>
      Spokane, WA 99281
    </div>

    <div class="contact-row">
      <span class="contact-item">
        <svg class="icon" viewBox="0 0 28 28" aria-hidden="true">
          <circle cx="14" cy="14" r="12" fill="none" stroke="var(--green)" stroke-width="2.5"/>
          <ellipse cx="14" cy="14" rx="5" ry="12" fill="none" stroke="var(--green)" stroke-width="2"/>
          <line x1="2" y1="14" x2="26" y2="14" stroke="var(--green)" stroke-width="2"/>
        </svg>
        <span>www.<span class="web-domain">summitaudiowell</span>.example</span>
      </span>
      <span class="contact-item">
        <svg class="icon" viewBox="0 0 28 28" aria-hidden="true">
          <circle cx="14" cy="14" r="12" fill="none" stroke="var(--green)" stroke-width="2.5"/>
          <path d="M10 8 q-2 2 0 7 q3 5 7 6 l2-2 -3-3 -2 1 q-2-2-3-4 l1-2z" fill="var(--green)"/>
        </svg>
        <span>509-617-2084</span>
      </span>
    </div>

    <div class="corner-decoration" role="img" aria-label="Decorative green swoosh ornament in the lower right corner"></div>
  </div>
</body>
</html>
```